Desert Basin Company Brochure

**** UPDATE 2-8-2014 ****

Size should be 11" X 17" or larger (tri or bi fold).

We're going to let the contest run it's full duration to allow for more time spent on designs.

No black backgrounds.

Consideration should be given to having the text be easy to read and in a nice, organized format.

*****************************

We're looking for an eye-catching, colorful brochure that will explain what we do, who we are... and what sets us apart from the competition.

Our company provides swimming pool service, repair, and custom renovations throughout the Phoenix, Arizona metropolitan area. These brochures will be hand-delivered to each prospective customer we visit.

The brochure will include images of our work, product logos, and a unique design that separates our company apart from the rest.

The brochure should be tri-fold. Although, if a designer wants to (or has better ideas) for a different lay-out, then we're open to seeing what can be done.

Colors we like: Blue, White, Silver, Copper, Green (accent color)

We like designs that are unique/different. Professional. Creative. Sleek. Sexy. Custom. We don't want the brochure to be "pretentious". We'd like for these brochures to leave a lasting impression with our prospective clients... and hopefully earn us more business.

We don't want the brochure to be too wordy, however if the designer feels we need to cut back (or add), let us know.

Our motto is "Every Ripple Counts".

You can view some of our projects, and what we're about either at our website (tidewellpools.example), Friendwall (www.facebook/tidewellpools), or Searchly+ (https://plus.google.com/+Tidewellpools). Thank you!

- Print-

(Front) Logo

Service - Repair - Renovation
555-347-9180
tidewellpools.example
service@tidewellpools.example
Like Us On Friendwall! Friendwall LOGO
Searchly Plus LOGO

(Body) Why Choose Us?

Thank you for the opportunity for our company to become your pool service provider!

We’re committed to providing the best customer service possible! At the end of the day you want your pool to be clean, clear, operational, and for your service provider to be available when you need them!

We’re licensed with the Sonoran Trades Licensing Board, Bonded, and Fully Insured.
A+ reviews with the Fair Merchant Council, Corra's Picks, Brivo, Olt, Friendwall, and Searchly!
All technicians are employees... not sub-contractors! Our employees are hard working, dependable, professional, and expected to follow our strict protocol for servicing your pool.
Flat-fee service rates! Any additional equipment repairs, maintenance, or chemical implementations are directly authorized by you!
No contracts! Our Service Level Agreement Form allows you to select your desired level of authorization for equipment repairs, filter maintenance, and extra chemical implementation programs.
Our uniformed technicians arrive in distinctive, clean GPS-tracked company trucks.
We leave detailed service slips after each service visit. In addition, all service visit information is electronically recorded and stored.
Easy, online account management to view and pay invoices or authorize estimates.
Invoices, estimates, questions, pictures, and video are communicated via e-mail!
Free service calls to diagnose equipment issues outside of our normal service.
10% Service Client Discount for all repairs and replacement items.
Tidewell Pools knows the importance of communication! We’re available by phone, email, or text all days of the week.

(Body) Our Methodology

We believe in 5 important factors in maintaining a clean, clear, and operational pool...

Good, Clean Water! Our local water supply contains high amounts of minerals. Pool chemicals add to this problem in a short amount of time. Our philosophy is to use the least amount of chemicals possible to achieve optimal water balance.
Efficient Water Flow! The invention of variable-speed pumps has enabled the ability to "dial in" proper water flow... while driving down energy costs.
Proper Filtration! Today’s high-capacity cartridge filters provide great filtration, save on wasted water from backwashing sand filters, and eliminate the need for water flow-restricting backwash valves.
Functioning Cleaning System! Having a working automatic cleaning system is vital in keeping the pool surface clean of debris and dirt... and free of staining.
A Dependable And Professional Pool Maintenance Technician! Our job is to not only oversee all of the items listed above... but to make sure your pool is in the best condition possible!

(Body) Equipment Repair & Installation

We’re educated on all phases of swimming pool equipment repair and installation... with a focus on energy-efficiency and optimum performance!

We’re an VRE & MQW Authorized Installer of variable-speed pool pumps. VRE & MQW trust us to properly install and calibrate all variable-speed pumps. We've been equipped to handle the new industry standards on variable-speed pumps since Arizona law went into effect January 1st, 2011.
We’re experts at acid washes and erasing the mineral build-up off of waterlines. All work is done in-house with our customized cleaning rig and trailer.
Heating systems. New efficiency standards have made installation and operation more affordable than ever.
Remote control automation systems. Technology now allows the user to easily view and control their entire pool system via a remote home computer, tablet, or phone!
Brilliant, color-changing LED lighting for pools and spas! The benefits of LED include brighter and broader displays... while lasting much longer than your typical light bulbs.
Salt systems provide a soft-water experience! In addition to the benefit of better feeling water, salt systems generate plenty of chlorine to keep your pool sanitized.

(Body) About Us

A native to Phoenix, Daniel Harrow founded Tidewell Pools in 2000. Our company was built from the ground up by way of hard work, word of mouth, and determination. Our company will always remain firmly grounded, and continue to develop systems that put our customers first!

Our philosophy is to treat every pool as if it were our own, run an efficient and organized business, and care for our employees.

Tidewell Pools is a yearly, proud contributor to the Saguaro Youth Clinic Swim Smart Day. Please educate and watch all children around water... every accident can be avoided.

(Back) Contact Us

Office: 555-347-9180 | Fax: 555-347-9186 | Email: service@tidewellpools.example
tidewellpools.example

Office / Warehouse Location
41572 West 8th Street, Suite 4
Phoenix, Arizona 85999
(NW of 8th Street & Mesquite Ridge Road)

AZ ROC: 731150, 731151, 731152, 604378

Target Market(s)

We target a market of pool owners, which typically have more disposable income.

30 - 75 years old.

Our clients range from first-time home buyers, self-employed, business professionals, doctors, landlords, thousandaires, millionaires.

Industry/Entity Type

Pool Service

Font styles to use
Serif

Colors
0355a3
cfdfed
ffffff
3176b5
eaf1f7

Requirements
Must have
• Must use provided images. We've included a few pool pictures, and will let you decide which ones to incorporate throughout the brochure.

Logos Used:
Tidewell Pools
Hydrovel
FMC
Corra's Picks
VRE
MQW
Saguaro Youth Clinic
Searchly+
Friendwall

Image pic of some of our trucks.

Nice to have
• Equipment images worked in.
Should not have
• Cartoonish fonts or design. No "Love" hearts!!

```html
<!DOCTYPE html>
<html lang="en">
<head>
<meta charset="utf-8">
<title>Tidewell Pools Brochure – Inside Spread</title>
<link rel="stylesheet" href="https://fonts.googleapis.com/css2?family=Bebas+Neue&family=Source+Sans+3:wght@400;600&display=swap">
<style>
  :root {
    --backdrop: #e9e9ea;
    --panel-light: #eaf1f7;
    --heading-blue: #0355a3;
    --band-blue: #0355a3;
    --body-text: #1e2b40;
    --title-cream: #ffffff;
    --title-box: rgba(3, 85, 163, 0.85);
    --frame-grey: #9fb4c8;
  }
  * { box-sizing: border-box; margin: 0; padding: 0; }
  html, body { width: 1200px; height: 857px; overflow: hidden; background: var(--backdrop); }
  .spread { position: absolute; left: 44px; top: 35px; width: 1114px; height: 788px; background: var(--panel-light); }
  .panel { position: absolute; top: 0; height: 768px; }
  .panel--left { left: 0; width: 371px; background: var(--panel-light); }
  .panel--center { left: 371px; width: 373px; }
  .panel--right { left: 744px; width: 370px; background: var(--panel-light); }
  .bottom-band { position: absolute; left: 0; bottom: 0; width: 100%; height: 20px; background: var(--band-blue); }

  .section-heading {
    display: inline-block; background: var(--heading-blue); color: #fff;
    font-family: "Bebas Neue", "Oswald", sans-serif; font-size: 18px; font-weight: 400; letter-spacing: 0.8px;
    line-height: 26px; height: 26px; padding: 0 8px; margin-bottom: 10px;
  }
  .copy {
    font-family: "Source Sans 3", "Myriad Pro", sans-serif; font-size: 12.6px; line-height: 13.7px;
    color: var(--body-text); text-align: justify;
  }
  .copy p { margin: 0; }
  .copy ul { list-style: none; }
  .copy li { margin-top: 2.4px; }
  .copy li::before { content: "• "; }

  .why-choose { position: absolute; left: 27px; top: 29px; width: 316px; }
  .methodology { position: absolute; left: 29px; top: 29px; width: 317px; }
  .equipment { position: absolute; left: 29px; top: 385px; width: 317px; }

  .thumb { position: absolute; top: 610px; width: 145px; height: 145px; border: 2px solid var(--frame-grey); }
  .thumb--desert { left: 28px; background: linear-gradient(180deg, #b9c6d3 0%, #8fa6ba 35%, #55716a 55%, #8a7c69 80%, #a3917a 100%); }
  .thumb--terrace { left: 196px; background: linear-gradient(180deg, #9ab0c2 0%, #7a6a55 30%, #3ea6c9 55%, #2b8fb1 75%, #a99b85 100%); }

  .pool-photo { position: absolute; inset: 0;
    background:
      linear-gradient(90deg, #8a7a67 0%, #a89480 9%, transparent 17%),
      linear-gradient(270deg, #cfc6b8 0%, #b8ad9d 8%, transparent 16%),
      linear-gradient(180deg, #3fa2c4 0%, #2f7fb0 25%, #2c5f93 50%, #2a5a86 70%, #3c6f8e 88%, #a79a88 100%);
  }
  .feature-title { position: absolute; right: 0; font-family: "Bebas Neue", "Oswald", sans-serif; font-weight: 400;
    color: var(--title-cream); background: var(--title-box); font-size: 54px; line-height: 71px; height: 71px; padding: 0 14px; letter-spacing: 1px; }
  .feature-title--top { top: 591px; width: 302px; }
  .feature-title--bottom { top: 665px; width: 258px; }
</style>
</head>
<body>
<main class="spread">
  <section class="panel panel--left">
    <div class="why-choose">
      <h2 class="section-heading">Why Choose Us?</h2>
      <div class="copy">
        <p>Thank you for the opportunity for our company to become your pool service provider!</p>
        <p>We’re committed to providing the best customer service possible! At the end of the day you want your pool to be clean, clear, operational, and for your service provider to be available when you need them!</p>
        <ul>
          <li>We’re licensed with the Sonoran Trades Licensing Board, Bonded, and Fully Insured.</li>
          <li>A+ reviews with the Fair Merchant Council, Corra's Picks, Brivo, Olt, Friendwall, and Searchly!</li>
          <li>All technicians are employees... not sub-contractors! Our employees are hard working, dependable, professional, and expected to follow our strict protocol for servicing your pool.</li>
          <li>Flat-fee service rates! Any additional equipment repairs, maintenance, or chemical implementations are directly authorized by you!</li>
          <li>No contracts! Our Service Level Agreement Form allows you to select your desired level of authorization for equipment repairs, filter maintenance, and extra chemical implementation programs.</li>
          <li>Our uniformed technicians arrive in distinctive, clean GPS-tracked company trucks.</li>
          <li>We leave detailed service slips after each service visit. In addition, all service visit information is electronically recorded and stored.</li>
          <li>Easy, online account management to view and pay invoices or authorize estimates.</li>
          <li>Invoices, estimates, questions, pictures, and video are communicated via e-mail!</li>
          <li>Free service calls to diagnose equipment issues outside of our normal service.</li>
          <li>10% Service Client Discount for all repairs and replacement items.</li>
          <li>Tidewell Pools knows the importance of communication! We’re available by phone, email, or text all days of the week.</li>
        </ul>
      </div>
    </div>
    <div class="thumb thumb--desert" role="img" aria-label="Photo of a natural desert-style pool with rock edging and spa under a cloudy sky"></div>
    <div class="thumb thumb--terrace" role="img" aria-label="Photo of a turquoise backyard pool with raised planter and potted agave"></div>
  </section>

  <section class="panel panel--center">
    <div class="pool-photo" role="img" aria-label="Photo looking down into a blue pool with a stone waterfall ledge and boulders"></div>
    <h1 class="feature-title feature-title--top">Another Title</h1>
    <p class="feature-title feature-title--bottom">Goes Here!</p>
  </section>

  <section class="panel panel--right">
    <div class="methodology">
      <h2 class="section-heading">Our Methodology</h2>
      <div class="copy">
        <p>We believe in 5 important factors in maintaining a clean, clear, and operational pool...</p>
        <ul>
          <li>Good, Clean Water! Our local water supply contains high amounts of minerals. Pool chemicals add to this problem in a short amount of time. Our philosophy is to use the least amount of chemicals possible to achieve optimal water balance.</li>
          <li>Efficient Water Flow! The invention of variable-speed pumps has enabled the ability to "dial in" proper water flow... while driving down energy costs.</li>
          <li>Proper Filtration! Today’s high-capacity cartridge filters provide great filtration, save on wasted water from backwashing sand filters, and eliminate the need for water flow-restricting backwash valves.</li>
          <li>Functioning Cleaning System! Having a working automatic cleaning system is vital in keeping the pool surface clean of debris and dirt... and free of staining.</li>
          <li>A Dependable And Professional Pool Maintenance Technician! Our job is to not only oversee all of the items listed above... but to make sure your pool is in the best condition possible!</li>
        </ul>
      </div>
    </div>
    <div class="equipment">
      <h2 class="section-heading">Equipment Repair &amp; Installation</h2>
      <div class="copy">
        <p>We’re educated on all phases of swimming pool equipment repair and installation... with a focus on energy-efficiency and optimum performance!</p>
        <ul>
          <li>We’re an VRE &amp; MQW Authorized Installer of variable-speed pool pumps. VRE &amp; MQW trust us to properly install and calibrate all variable-speed pumps. We've been equipped to handle the new industry standards on variable-speed pumps since Arizona law went into effect January 1st, 2011.</li>
          <li>We’re experts at acid washes and erasing the mineral build-up off of waterlines. All work is done in-house with our customized cleaning rig and trailer.</li>
          <li>Heating systems. New efficiency standards have made installation and operation more affordable than ever.</li>
          <li>Remote control automation systems. Technology now allows the user to easily view and control their entire pool system via a remote home computer, tablet, or phone!</li>
          <li>Brilliant, color-changing LED lighting for pools and spas! The benefits of LED include brighter and broader displays... while lasting much longer than your typical light bulbs.</li>
          <li>Salt systems provide a soft-water experience! In addition to the benefit of better feeling water, salt systems generate plenty of chlorine to keep your pool sanitized.</li>
        </ul>
      </div>
    </div>
  </section>

  <div class="bottom-band"></div>
</main>
</body>
</html>
```